Tellmora Corporate Stationery

Look for design of all new corporate stationery for an existing insurance broking business that is going through a redesign and move from older partners to younger family members. New Logo is attached. Company is Brisbane based.
Colours in the Logo is Hex #43bed8 and website features a lot of hex #17b8d8. Website front page "A plan to protect you" - headline. "Professional and Individual advice to protect your greatest assets" - tagline.

Stationery required: Business Cards, Letter head, Thank-you cards, Birthday cards, Presentation folders, With Compliment slips and a powerpoint template. We also would like to send a card to all customers with the something along of the lines of "something new".

Target Market(s)

Customers of Insurance business looking at superannuation, life and income protection insurance, investment advice and wills

Industry/Entity Type

Insurance Broker

Font styles to use
Other font styles liked:
• same as logo

Requirements
Must have
• The above designs for new stationery for the new business including:
• Business Cards, Letter head, Thank-you cards, Birthday cards, Presentation folders, With Compliment slips and a powerpoint template. We also would like to send a card to all customers with the something along of the lines of "something new".
Nice to have
• It is a new look - long time family business being passed to next generation - big focus on advice for YOU, individual advice etc..

```html
<!DOCTYPE html>
<html lang="en">
<head>
<meta charset="utf-8">
<title>Tellmora Financial Group – Business Card</title>
<link href="https://fonts.googleapis.com/css2?family=Ubuntu:ital,wght@0,300;0,400;0,500;1,400&display=swap" rel="stylesheet">
<style>
  :root {
    --brand-blue: #43bed8;
    --ink-grey: #7d7f82;
    --pill-grey: #eeeeef;
    --pattern-grey: #ededee;
    --canvas: #ffffff;
    --card: #ffffff;
  }
  * { margin: 0; padding: 0; box-sizing: border-box; }
  html, body {
    width: 1200px; height: 1000px; overflow: hidden;
    background: var(--canvas);
    font-family: "Ubuntu", sans-serif;
  }
  .stage { position: relative; width: 1200px; height: 1000px; }
  .card {
    position: absolute; left: 205px; width: 788px;
    background: var(--card);
    box-shadow: 0 1px 6px rgba(0,0,0,0.18);
    overflow: hidden;
  }
  .card--front { top: 0; height: 487px; }
  .card--back { top: 513px; height: 487px; }

  /* front */
  .front-pattern {
    position: absolute; inset: 0;
    background: linear-gradient(135deg, #f1f1f2 0%, var(--pattern-grey) 50%, #f3f3f4 100%);
  }
  .wordmark-panel {
    position: absolute; left: 98px; top: 268px; width: 592px; height: 140px;
    background: var(--card); border-radius: 40px;
  }
  .wordmark-dot {
    position: absolute; left: 298px; top: 85px; width: 190px; height: 190px;
    border-radius: 50%; background: var(--card);
    border: 14px solid var(--ink-grey);
  }
  .wordmark {
    position: absolute; left: 98px; width: 592px; text-align: center;
    color: var(--brand-blue); font-weight: 500; text-transform: uppercase;
    white-space: nowrap;
  }
  .wordmark__name { top: 278px; font-size: 78px; letter-spacing: 19px; padding-left: 19px; }
  .wordmark__descriptor { top: 352px; font-size: 40px; letter-spacing: 8px; padding-left: 8px; }

  /* back */
  .back-pattern {
    position: absolute; inset: 0;
    background: linear-gradient(135deg, #fafafa 0%, #f4f4f5 60%, #fafafa 100%);
  }
  .band {
    position: absolute; left: 33px; background: var(--brand-blue);
    border-radius: 27px 0 0 27px; color: #fff;
  }
  .band--name { top: 50px; width: 560px; height: 54px; }
  .band--title { top: 111px; width: 560px; height: 54px; }
  .band__rule {
    position: absolute; left: 63px; top: 106px; width: 502px; height: 3px; background: #fff;
  }
  .person-name {
    position: absolute; left: 63px; top: 50px; font-size: 51px; font-weight: 400; color: #fff; line-height: 54px;
  }
  .person-title {
    position: absolute; left: 62px; top: 111px; font-size: 33px; font-weight: 300; color: #fff; line-height: 54px; letter-spacing: 0.8px;
  }
  .badge {
    position: absolute; left: 575px; top: 10px; width: 180px; height: 180px; border-radius: 50%;
    background: var(--brand-blue); display: flex; align-items: center; justify-content: center;
  }
  .badge__inner {
    width: 152px; height: 152px; border-radius: 50%; background: #fff;
    display: flex; align-items: center; justify-content: center;
    color: var(--brand-blue); font-weight: 500; font-size: 26px;
  }
  .tagline-tab {
    position: absolute; left: 578px; top: 160px; width: 165px; height: 285px;
    background: #f2f2f2; border-radius: 0 0 20px 20px;
  }
  .tagline-tab__fill {
    position: absolute; left: 12px; top: 12px; right: 12px; bottom: 12px;
    background: var(--brand-blue); border-radius: 0 0 12px 12px;
    display: flex; align-items: flex-start; justify-content: center; padding-top: 38px;
  }
  .tagline {
    color: #fff; font-style: italic; font-size: 19px; line-height: 29.5px; text-align: center; width: 135px;
  }
  .contact-list { list-style: none; }
  .contact {
    position: absolute; left: 33px; width: 542px; height: 40px;
    background: var(--pill-grey); border-radius: 20px;
    display: flex; align-items: center;
  }
  .contact__icon { position: absolute; left: 38px; width: 54px; height: 44px; display: flex; justify-content: center; align-items: center; }
  .contact__icon svg { fill: var(--ink-grey); }
  .contact__text {
    position: absolute; left: 107px; font-size: 25px; color: var(--ink-grey); letter-spacing: 1px;
    white-space: nowrap;
  }
</style>
</head>
<body>
<main class="stage">

  <section class="card card--front" aria-label="Business card front">
    <div class="front-pattern" role="img" aria-label="Light grey diagonal dash pattern background"></div>
    <div class="wordmark-dot"></div>
    <div class="wordmark-panel"></div>
    <div class="wordmark wordmark__name">Tellmora</div>
    <div class="wordmark wordmark__descriptor">Financial Group</div>
  </section>

  <section class="card card--back" aria-label="Business card back">
    <div class="back-pattern" role="img" aria-label="Faint grey rounded link pattern background"></div>

    <div class="band band--name"></div>
    <div class="band band--title"></div>
    <div class="band__rule"></div>
    <h1 class="person-name">Jane Doe</h1>
    <p class="person-title">Financial Advisor</p>

    <div class="tagline-tab">
      <div class="tagline-tab__fill">
        <p class="tagline">“Professional<br>and<br>individual<br>advice to<br>protect your<br>greatest<br>assets”</p>
      </div>
    </div>
    <div class="badge"><div class="badge__inner">Tellmora</div></div>

    <ul class="contact-list">
      <li class="contact" style="top:210px">
        <span class="contact__icon">
          <svg width="50" height="40" viewBox="0 0 50 40" aria-hidden="true">
            <polygon points="25,2 48,20 43,20 25,7 7,20 2,20"/>
            <path d="M10 20 L25 9 L40 20 V38 H30 V27 H20 V38 H10 Z"/>
          </svg>
        </span>
        <span class="contact__text">47 Parkvale Terrace St. Brisbane</span>
      </li>
      <li class="contact" style="top:270px">
        <span class="contact__icon">
          <svg width="22" height="44" viewBox="0 0 22 44" aria-hidden="true">
            <path d="M6 2 H13 V12 H10 C8 18 8 26 10 32 H13 V42 H6 C0 34 0 10 6 2 Z"/>
          </svg>
        </span>
        <span class="contact__text">(07) 5550 4821</span>
      </li>
      <li class="contact" style="top:330px">
        <span class="contact__icon">
          <svg width="52" height="36" viewBox="0 0 52 36" aria-hidden="true">
            <path d="M1 1 H51 L26 20 Z"/>
            <path d="M1 5 L19 19 L1 35 Z"/>
            <path d="M51 5 L33 19 L51 35 Z"/>
            <path d="M22 21 L26 24 L30 21 L48 35 H4 Z"/>
          </svg>
        </span>
        <span class="contact__text">contact@tellmorafinancesite.com</span>
      </li>
      <li class="contact" style="top:390px">
        <span class="contact__icon">
          <svg width="44" height="44" viewBox="0 0 44 44" aria-hidden="true">
            <circle cx="22" cy="22" r="20" fill="none" stroke="#7d7f82" stroke-width="3"/>
            <path d="M12 10 C17 8 20 12 18 16 C15 19 20 22 17 27 C14 30 10 24 8 20 C7 15 9 12 12 10 Z"/>
            <path d="M25 8 C30 9 35 13 36 18 C33 19 30 17 28 20 C30 24 34 24 33 30 C31 35 27 37 25 34 C24 29 22 26 24 22 C21 19 22 14 25 8 Z"/>
          </svg>
        </span>
        <span class="contact__text">www.tellmorafinancesite.com</span>
      </li>
    </ul>
  </section>

</main>
</body>
</html>
```